" Fornecemos infra estrutura para empresas, possuímos uma rede de fibra óptica própria cobrindo diversas cidades, provendo conexão a internet, telefonia voip, transporte de dados, temos um datacenter, fornecemos soluções de cloud computing, cloud pabx. "

```html
<!DOCTYPE html>
<html lang="pt-BR">
<head>
<meta charset="UTF-8">
<title>Assinatura de e-mail — Velora Telecom</title>
<link rel="stylesheet" href="https://fonts.googleapis.com/css2?family=Open+Sans:wght@400;600;700&display=swap">
<style>
  :root {
    --page-bg: #e9ebee;
    --card-top: #ffffff;
    --card-bottom: #eceef0;
    --navy: #1c2050;
    --blue: #1a9ad6;
    --text: #2b2d35;
    --muted: #6b6e76;
  }
  * { margin: 0; padding: 0; box-sizing: border-box; }
  html, body {
    width: 1200px;
    height: 1200px;
    overflow: hidden;
    background: var(--page-bg);
    font-family: "Open Sans", Arial, sans-serif;
  }
  .signature {
    position: absolute;
    left: 100px;
    top: 440px;
    width: 1000px;
    height: 320px;
    background: linear-gradient(180deg, var(--card-top) 0%, var(--card-bottom) 100%);
    box-shadow: 0 6px 18px rgba(0,0,0,0.12);
  }
  .identity {
    position: absolute;
    left: 70px;
    top: 70px;
    width: 400px;
    text-align: center;
  }
  .brand {
    display: flex;
    align-items: center;
    justify-content: center;
    gap: 16px;
    height: 100px;
  }
  .brand-dot {
    width: 72px;
    height: 72px;
    border-radius: 50%;
    background: var(--blue);
  }
  .brand-name {
    font-weight: 700;
    font-size: 40px;
    letter-spacing: 2px;
    color: var(--navy);
    line-height: 1;
  }
  .person-name {
    margin-top: 32px;
    font-weight: 700;
    font-size: 25px;
    color: var(--text);
  }
  .person-role {
    margin-top: 8px;
    font-size: 14px;
    letter-spacing: 1px;
    color: var(--muted);
  }
  .contacts {
    position: absolute;
    left: 540px;
    top: 36px;
    list-style: none;
  }
  .contact {
    display: flex;
    align-items: flex-start;
    gap: 18px;
    font-size: 25px;
    color: var(--text);
    margin-bottom: 20px;
    line-height: 34px;
  }
  .contact svg { flex: 0 0 26px; margin-top: 4px; fill: var(--text); }
  .contact-address { font-size: 21px; line-height: 28px; }
  .bands {
    position: absolute;
    left: 0;
    bottom: 0;
    width: 1000px;
    height: 40px;
  }
</style>
</head>
<body>
  <section class="signature">
    <div class="identity">
      <div class="brand">
        <span class="brand-dot"></span>
        <span class="brand-name">VELORA TELECOM</span>
      </div>
      <p class="person-name">Nome Sobrenome</p>
      <p class="person-role">FUNÇÃO</p>
    </div>

    <ul class="contacts">
      <li class="contact">
        <svg width="26" height="26" viewBox="0 0 24 24"><path d="M2 5h20v14H2z M3.5 6.5v.3l8.5 6 8.5-6v-.3z" fill-rule="evenodd"/></svg>
        <span>contato@empresa.com.br</span>
      </li>
      <li class="contact">
        <svg width="26" height="26" viewBox="0 0 24 24"><path d="M3 9c0-3 4-5 9-5s9 2 9 5v2h-5V9H8v2H3z M6 12h12l2 8H4z"/></svg>
        <span>(xx) x xxxx-xxxx</span>
      </li>
      <li class="contact">
        <svg width="26" height="26" viewBox="0 0 24 24"><path d="M7 2h10a1 1 0 0 1 1 1v18a1 1 0 0 1-1 1H7a1 1 0 0 1-1-1V3a1 1 0 0 1 1-1z M8 4v14h8V4z M11 19.5h2v1h-2z" fill-rule="evenodd"/></svg>
        <span>(xx) x xxxx-xxxx</span>
      </li>
      <li class="contact contact-address">
        <svg width="26" height="26" viewBox="0 0 24 24"><path d="M12 2a7 7 0 0 1 7 7c0 5-7 13-7 13S5 14 5 9a7 7 0 0 1 7-7z M12 6.5a2.5 2.5 0 1 0 0 5 2.5 2.5 0 0 0 0-5z" fill-rule="evenodd"/></svg>
        <span>Rua desconhecida, xxxx<br>desconhecido</span>
      </li>
    </ul>

    <svg class="bands" viewBox="0 0 1000 40" preserveAspectRatio="none">
      <rect x="0" y="14" width="720" height="12" fill="var(--blue)"/>
      <polygon points="715,14 1000,14 1000,40 690,40" fill="var(--navy)"/>
    </svg>
  </section>
</body>
</html>
```